real esate business card with company logo and name

we need a business card design for a real esate company

The company name is Walsh & Brand Pty Ltd, and we have our logo designed and will upload. We want classic or moden feel. Black or white background. looks more textured. Should include folowinginformations
Owen Walsh and Lucy Brand
Sales Agents & Onsite Manager
p: 07 5948 2063
F: 07 5948 2174
M:0431 857 219
3/42 Marlow Crescent, FERNLEA QLD 4213

We want this business card looks professonal. Thank you in advance.

Industry/Entity Type

Real Estate Agent

Contact Information for Business Card

Owen Walsh and Lucy Brand
Onsite Manager & Sales Agents
p: 07 5948 2063
M:0431 857 219

Font styles to use
Serif

Colors
000000
fbfbfb
333333
959595

Requirements
Must have
• company logo and name, black or white back ground

```html
<!DOCTYPE html>
<html lang="en">
<head>
<meta charset="utf-8">
<title>Walsh &amp; Brand Pty Ltd – Business Card</title>
<link rel="stylesheet" href="https://fonts.googleapis.com/css2?family=Cinzel:wght@400;700&family=Raleway:wght@300;400&display=swap">
<style>
  :root {
    --ink: #000000;
    --paper: #fbfbfb;
    --charcoal: #333333;
    --steel: #959595;
    --backdrop: #e6e6e6;
  }
  * { margin: 0; padding: 0; box-sizing: border-box; }
  html, body { width: 1200px; height: 913px; overflow: hidden; }
  body { background: var(--backdrop); position: relative; }

  .card {
    position: absolute;
    width: 600px;
    height: 343px;
    overflow: hidden;
    box-shadow: 0 10px 28px rgba(0,0,0,0.25);
  }

  /* Front */
  .card--front {
    left: 60px; top: 80px;
    background: linear-gradient(180deg, var(--paper) 0%, #f1f1f1 100%);
    color: var(--charcoal);
  }
  .front__base-band {
    position: absolute; left: 0; bottom: 0;
    width: 352px; height: 60px;
    background: var(--ink);
  }
  .front__corner-block {
    position: absolute; right: 0; bottom: 0;
    width: 248px; height: 116px;
    background: var(--steel);
  }
  .brand {
    position: absolute; left: 42px; top: 118px;
    display: flex; align-items: center; gap: 10px;
  }
  .brand__square {
    width: 26px; height: 26px;
    background: var(--charcoal);
  }
  .brand__name {
    font-family: 'Cinzel', serif;
    font-weight: 700;
    font-size: 15px;
    letter-spacing: 0.5px;
    color: var(--ink);
  }
  .contact {
    position: absolute; left: 42px; top: 178px;
    width: 260px;
    border-top: 1.5px solid var(--charcoal);
    padding-top: 10px;
    font-family: 'Raleway', sans-serif;
    font-size: 12.5px;
    color: var(--charcoal);
  }
  .contact__row { display: flex; align-items: center; gap: 8px; line-height: 20px; }
  .contact__icon { width: 11px; height: 11px; fill: var(--charcoal); }

  .agents {
    position: absolute; right: 34px; top: 44px;
    width: 300px;
    text-align: right;
  }
  .agents__names {
    font-family: 'Cinzel', serif;
    font-size: 20px;
    color: var(--charcoal);
    letter-spacing: 0.3px;
  }
  .agents__role {
    font-family: 'Cinzel', serif;
    font-size: 10.5px;
    color: var(--steel);
    letter-spacing: 0.6px;
    margin-top: 2px;
  }
  .agents__rule {
    height: 1.5px; background: var(--charcoal);
    margin: 8px 0 0 -70px;
  }
  .address {
    position: absolute; right: 34px; top: 128px;
    text-align: right;
    font-family: 'Cinzel', serif;
    color: var(--charcoal);
  }
  .address__street { font-size: 11px; letter-spacing: 0.4px; }
  .address__locality { font-size: 13px; font-weight: 700; margin-top: 3px; }

  /* Back */
  .card--back {
    left: 540px; top: 490px;
    background: linear-gradient(160deg, #2a2a2a 0%, var(--ink) 70%);
    display: flex; flex-direction: column; align-items: center; justify-content: center;
    gap: 18px;
  }
  .back__square {
    width: 70px; height: 70px;
    background: var(--steel);
  }
  .back__name {
    font-family: 'Raleway', sans-serif;
    font-weight: 300;
    font-size: 20px;
    letter-spacing: 3px;
    text-transform: uppercase;
    color: var(--steel);
  }
</style>
</head>
<body>

  <section class="card card--front" aria-label="Business card front">
    <div class="front__base-band"></div>
    <div class="front__corner-block"></div>

    <div class="brand">
      <span class="brand__square"></span>
      <span class="brand__name">WALSH &amp; BRAND PTY LTD.</span>
    </div>

    <div class="contact">
      <div class="contact__row">
        <svg class="contact__icon" viewBox="0 0 24 24"><path d="M6.6 10.8a15 15 0 0 0 6.6 6.6l2.2-2.2a1 1 0 0 1 1-.25 11.4 11.4 0 0 0 3.6.57 1 1 0 0 1 1 1V20a1 1 0 0 1-1 1A17 17 0 0 1 3 4a1 1 0 0 1 1-1h3.5a1 1 0 0 1 1 1c0 1.25.2 2.45.57 3.57a1 1 0 0 1-.25 1z"/></svg>
        <span>07 5948 2063</span>
      </div>
      <div class="contact__row">
        <svg class="contact__icon" viewBox="0 0 24 24"><path d="M6 2h10v5H6zM3 8h18v10H3zm3 9h12v5H6z"/></svg>
        <span>07 5948 2174</span>
      </div>
      <div class="contact__row">
        <svg class="contact__icon" viewBox="0 0 24 24"><path d="M7 1h10a2 2 0 0 1 2 2v18a2 2 0 0 1-2 2H7a2 2 0 0 1-2-2V3a2 2 0 0 1 2-2zm0 3v14h10V4z"/></svg>
        <span>0431 857 219</span>
      </div>
    </div>

    <div class="agents">
      <div class="agents__names">Owen Walsh &amp; Lucy Brand</div>
      <div class="agents__role">Sales Agents &amp; Onsite Manager</div>
      <div class="agents__rule"></div>
    </div>

    <div class="address">
      <div class="address__street">3/42 Marlow Crescent</div>
      <div class="address__locality">FERNLEA QLD 4213</div>
    </div>
  </section>

  <section class="card card--back" aria-label="Business card back">
    <span class="back__square"></span>
    <span class="back__name">Walsh &amp; Brand Pty Ltd.</span>
  </section>

</body>
</html>
```